Copperbend Blazeworks Website Design

I am looking for a website design ( Home page and inner template page ) in a .psd format. The home page needs to have a large hero image what will function as a "slider", and have some highlight graphical areas/links to the following links "Public & Municipal Events", "Corporate Events", "Special Events". The main navigation needs to have the following nav links "gallery", "home", "about", "services" and "contact". Unfortunately the client does not have any nice hi-rez images ( this is a company that specializes is large fireworks displays ) so please use stock photography sample images from snapvaultpics since we have an account there an can purchase the photos if our client wants to use them. Our current full time graphic artist has been with us for a long time so we are looking at artflockhub as a way to add a fresh approach to design and possibly find someone we can work with regularly. Here is a few designs that in the way we display them for our clients for approval. As you can see there are a couple that don't have their own images so they are utilizing the before mentioned snapvaultpics samples. On the plus side we did manage to get their logo in a .ai format. We have our team for handling the conversion from design to html.

http://reedfoxbuildstudio.com/dev/

```html
<!DOCTYPE html>
<html lang="en">
<head>
<meta charset="utf-8">
<title>Copperbend Blazeworks</title>
<link href="https://fonts.googleapis.com/css2?family=Oswald:wght@500;600&family=Lato:wght@400;700&family=Roboto:wght@400;500&display=swap" rel="stylesheet">
<style>
:root{
  --ink:#111111;
  --text:#444444;
  --accent:#4aa8e0;
  --white:#ffffff;
  --footer:#161616;
  --footer-line:#3a3a3a;
  --muted:#dddddd;
}
*{box-sizing:border-box;margin:0;padding:0}
html,body{width:1200px;height:2325px;overflow:hidden}
body{position:relative;background:var(--white);font-family:'Lato',sans-serif;color:var(--text)}
.abs{position:absolute}

/* header */
.site-header{left:0;top:0;width:1200px;height:104px;background:var(--white)}
.brand{left:118px;top:30px;display:flex;align-items:center;gap:8px;font-family:'Lato',sans-serif;font-size:19px;color:#333;font-weight:400}
.brand .dot{width:14px;height:14px;border-radius:50%;background:var(--accent)}
.phone{left:693px;top:11px;display:flex;align-items:center;gap:8px;font-family:'Roboto',sans-serif;font-size:22px;color:var(--ink)}
.phone .badge{width:42px;height:42px;border-radius:50%;background:var(--accent);display:flex;align-items:center;justify-content:center}
.divider{left:897px;top:15px;width:1px;height:37px;background:#bbb}
.socials-top{left:916px;top:13px;display:flex;gap:6px}
.socials-top span{width:39px;height:39px;border:1px solid #aaa;border-radius:50%}
.main-nav{left:517px;top:72px;display:flex;gap:0;font-family:'Roboto',sans-serif;font-size:16px;color:var(--ink);font-weight:500}
.main-nav a{color:inherit;text-decoration:none}
.main-nav a+a{margin-left:65px}

/* hero */
.hero{left:0;top:104px;width:1200px;height:618px;background:radial-gradient(ellipse at 62% 40%,#8a1c52 0%,#3a0d3a 30%,#0b0a1c 62%,#000 100%)}
.hero h1{left:110px;top:212px;font-family:'Oswald',sans-serif;font-weight:600;font-size:46px;color:var(--white);letter-spacing:.5px}
.hero p{left:113px;top:274px;width:440px;font-size:16.5px;line-height:28px;color:var(--white)}
.hero .btn-outline{left:111px;top:349px;width:142px;height:46px;border:2px solid var(--white);border-radius:3px;color:var(--white);font-family:'Roboto',sans-serif;font-size:16px;font-weight:500;display:flex;align-items:center;justify-content:center}
.dots{left:563px;top:573px;display:flex;gap:9px}
.dots span{width:11px;height:11px;border-radius:50%;background:rgba(255,255,255,.45)}
.dots span:first-child{background:var(--white)}

/* about */
.about-photo{left:128px;top:807px;width:457px;height:420px;background:linear-gradient(180deg,#1d1a4a 0%,#6b2f7a 45%,#3a2a1a 75%,#1a140c 100%)}
.about h2{left:636px;top:860px;font-family:'Oswald',sans-serif;font-weight:600;font-size:41px;color:var(--ink)}
.about p{left:636px;top:923px;width:460px;font-size:15px;line-height:28.3px;color:var(--text)}
.btn-fill{left:636px;top:1119px;width:142px;height:46px;background:var(--accent);border-radius:3px;color:var(--white);font-family:'Roboto',sans-serif;font-size:16px;font-weight:500;display:flex;align-items:center;justify-content:center}

/* services */
.services-title{left:0;top:1296px;width:1200px;text-align:center;font-family:'Oswald',sans-serif;font-weight:600;font-size:41px;color:var(--ink)}
.card{top:1369px;width:316px}
.card .photo{height:372px}
.card h3{margin-top:20px;text-align:center;font-family:'Lato',sans-serif;font-weight:400;font-size:17.5px;color:var(--ink);text-transform:uppercase}
.card p{margin-top:10px;text-align:center;font-size:13px;line-height:26px;color:var(--text)}
.p1{background:linear-gradient(160deg,#e9c07a 0%,#6e5a3e 45%,#2a2a30 100%)}
.p2{background:linear-gradient(160deg,#5a4036 0%,#6a7078 50%,#2b2f36 100%)}
.p3{background:linear-gradient(180deg,#2a2a4a 0%,#8a8292 45%,#d9d4dc 75%,#3a3650 100%)}

/* footer */
.site-footer{left:0;top:1965px;width:1200px;height:360px;background:var(--footer);color:var(--white)}
.f-brand{left:110px;top:2110px;font-size:19px;color:var(--white)}
.f-socials{left:122px;top:2178px;display:flex;gap:5px}
.f-socials span{width:33px;height:33px;border-radius:50%;background:var(--white)}
.f-col h4{font-family:'Lato',sans-serif;font-weight:700;font-size:16.5px;color:var(--white);letter-spacing:-.2px}
.f-col h4::after{content:"";display:block;width:72px;height:2px;background:var(--accent);margin-top:8px}
.f-col ul{list-style:none;margin-top:16px}
.f-col li{font-size:13.5px;line-height:28.3px;color:var(--white)}
.contact-row{display:flex;gap:10px;align-items:flex-start;font-size:13.5px;line-height:22px;margin-top:12px}
.contact-row .ic{flex:none;width:26px;height:26px;border-radius:50%;background:#2c2c2c;display:flex;align-items:center;justify-content:center}
.subscribe p{margin-top:16px;font-size:13.5px;line-height:28px;width:260px}
.sub-form{margin-top:18px;display:flex;width:263px;height:48px}
.sub-form .field{flex:1;background:var(--white);border-radius:3px 0 0 3px;display:flex;align-items:center;gap:7px;padding-left:17px;font-family:'Roboto',sans-serif;font-size:14px;color:#888}
.sub-form .send{width:48px;background:var(--accent);border-radius:0 3px 3px 0;display:flex;align-items:center;justify-content:center}
.f-line{left:103px;top:2269px;width:977px;height:1px;background:var(--footer-line)}
.copyright{left:0;top:2287px;width:1200px;text-align:center;font-size:13.5px;color:var(--white)}
</style>
</head>
<body>

<header class="site-header abs">
  <div class="brand abs"><span class="dot"></span>Copperbend Blazeworks</div>
  <div class="phone abs">
    <span class="badge"><svg width="20" height="20" viewBox="0 0 24 24"><path d="M6.6 10.8a15 15 0 0 0 6.6 6.6l2.2-2.2c.3-.3.7-.4 1-.2 1.1.4 2.3.6 3.6.6.6 0 1 .4 1 1V20c0 .6-.4 1-1 1A17 17 0 0 1 3 4c0-.6.4-1 1-1h3.5c.6 0 1 .4 1 1 0 1.3.2 2.5.6 3.6.1.3 0 .7-.2 1z" fill="#fff"/></svg></span>
    888 888 8888
  </div>
  <div class="divider abs"></div>
  <div class="socials-top abs"><span></span><span></span><span></span><span></span></div>
  <nav class="main-nav abs"><a>HOME</a><a>ABOUT</a><a>SERVICES</a><a>GALLERY</a><a>CONTACT</a></nav>
</header>

<section class="hero abs" role="img" aria-label="Colourful fireworks display bursting over a lake at night">
  <h1 class="abs">COPPERBEND BLAZEWORKS</h1>
  <p class="abs">Lorem ipsum dolor sit amet, consectetur adipiscing elit, sed do eiusmod tempor incididunt et dolore magna aliqua.</p>
  <div class="btn-outline abs">GET STARTED</div>
  <svg class="abs" style="left:63px;top:288px" width="24" height="44" viewBox="0 0 24 44"><path d="M22 2 2 22l20 20" fill="none" stroke="#fff" stroke-width="2"/></svg>
  <svg class="abs" style="left:1107px;top:288px" width="24" height="44" viewBox="0 0 24 44"><path d="m2 2 20 20L2 42" fill="none" stroke="#fff" stroke-width="2"/></svg>
  <div class="dots abs"><span></span><span></span><span></span><span></span></div>
</section>

<section class="about">
  <div class="about-photo abs" role="img" aria-label="Fireworks exploding above a lit historic gate at night"></div>
  <h2 class="abs">ABOUT US</h2>
  <p class="abs">Lorem ipsum dolor sit amet, consectetur adipis elit, sed do eiusmod tempor incididunt ut labore e magna aliqua. Quis ipsum suspendisse ultrices gravida. Risus commodo viverra maecenas accumsan lacus vel facilisis. Lorem ipsum dolor sit amet, consectetur adipis elit, sed do eiusmod tempor incididunt ut labore e magna aliqua. Quis ipsum suspendisse ultrices gravida.</p>
  <div class="btn-fill abs">LEARN MORE</div>
</section>

<section class="services">
  <h2 class="services-title abs">OUR SERVICES</h2>
  <article class="card abs" style="left:111px">
    <div class="photo p1" role="img" aria-label="Saxophone players performing at an outdoor festival"></div>
    <h3>Public &amp; Municipal Events</h3>
    <p>Lorem ipsum dolor amet, consectetur adipisci elit, sed do mod tempor incididunt ut labore et dolore magna aliqua. Quis ipsum suspendie ultrices gravida. Risus commodo viverra maecenas accumsan</p>
  </article>
  <article class="card abs" style="left:442px">
    <div class="photo p2" role="img" aria-label="Colleagues mingling with drinks at a corporate gathering"></div>
    <h3>Corporate Events</h3>
    <p>Lorem ipsum dolor amet, consectetur adipisci elit, sed do mod tempor incididunt ut labore et dolore magna aliqua. Quis ipsum suspendie ultrices gravida. Risus commodo viverra maecenas accumsan</p>
  </article>
  <article class="card abs" style="left:773px">
    <div class="photo p3" role="img" aria-label="Elegant banquet hall with a decorated round table and chandeliers"></div>
    <h3>Special Events</h3>
    <p>Lorem ipsum dolor amet, consectetur adipisci elit, sed do mod tempor incididunt ut labore et dolore magna aliqua. Quis ipsum suspendie ultrices gravida. Risus commodo viverra maecenas accumsan</p>
  </article>
</section>

<footer class="site-footer abs"></footer>
<div class="f-brand abs">Copperbend Blazeworks</div>
<div class="f-socials abs"><span></span><span></span><span></span><span></span></div>

<div class="f-col abs" style="left:349px;top:2040px">
  <h4>QUICK LINKS</h4>
  <ul><li>Home</li><li>Gallery</li><li>About</li><li>Services</li><li>Contact</li></ul>
</div>

<div class="f-col abs" style="left:537px;top:2040px">
  <h4>CONTACT US</h4>
  <div style="margin-top:16px">
    <div class="contact-row"><span class="ic"><svg width="10" height="14" viewBox="0 0 10 14"><path d="M5 0a5 5 0 0 0-5 5c0 4 5 9 5 9s5-5 5-9a5 5 0 0 0-5-5zm0 7a2 2 0 1 1 0-4 2 2 0 0 1 0 4z" fill="#fff"/></svg></span><span>1234 Somestreet Anywhere<br>USA 21212</span></div>
    <div class="contact-row"><span class="ic"><svg width="12" height="12" viewBox="0 0 24 24"><path d="M6.6 10.8a15 15 0 0 0 6.6 6.6l2.2-2.2c.3-.3.7-.4 1-.2 1.1.4 2.3.6 3.6.6.6 0 1 .4 1 1V20c0 .6-.4 1-1 1A17 17 0 0 1 3 4c0-.6.4-1 1-1h3.5c.6 0 1 .4 1 1 0 1.3.2 2.5.6 3.6.1.3 0 .7-.2 1z" fill="#fff"/></svg></span><span style="line-height:26px">888 888 8888</span></div>
    <div class="contact-row"><span class="ic"><svg width="13" height="10" viewBox="0 0 13 10"><rect x=".5" y=".5" width="12" height="9" fill="none" stroke="#fff"/><path d="m.5.5 6 5 6-5" fill="none" stroke="#fff"/></svg></span><span style="line-height:26px">info@copperbendblazeworks.com</span></div>
  </div>
</div>

<div class="f-col subscribe abs" style="left:816px;top:2040px">
  <h4>SUBSCRIBE TO OUR BLOG</h4>
  <p>Sign up today to get resources on how to attract and retain more customers!</p>
  <div class="sub-form">
    <div class="field"><svg width="14" height="11" viewBox="0 0 13 10"><rect x=".5" y=".5" width="12" height="9" fill="none" stroke="#888"/><path d="m.5.5 6 5 6-5" fill="none" stroke="#888"/></svg>Email Address</div>
    <div class="send"><svg width="18" height="18" viewBox="0 0 24 24"><path d="M22 2 2 11l7 3 2 8 3-6 6 3z" fill="#fff"/></svg></div>
  </div>
</div>

<div class="f-line abs"></div>
<div class="copyright abs">Copyright © 2021. Copperbend Blazeworks Reserved</div>

</body>
</html>
```